Whitcombe Business Card Design

The name of the business is Dario Whitcombe, CPA LLC
The service that we offer is Accounting, Tax & Consulting Services. I need it to have the following items:
Dario Whitcombe, Principal
Phone Number
Email Address
Physical Address

I have attached the company logo, one in black and one in white. Please provide a design in black background and the other in white background. Please include "Accounting, Tax & Consulting Services". I want the business card to be clean and very professional.

```html
<!DOCTYPE html>
<html lang="en">
<head>
<meta charset="utf-8">
<title>Dario Whitcombe, CPA LLC — Business Card</title>
<link href="https://fonts.googleapis.com/css2?family=Montserrat:wght@400;500;600&display=swap" rel="stylesheet">
<style>
  :root {
    --page-bg: #e4e5e4;
    --card-black: #000000;
    --card-white: #ffffff;
    --stripe: #2b2623;
    --ink-light: #f2f2f2;
    --ink-dark: #2d2d2d;
    --ink-grey: #8a8a8a;
    --accent-red: #9b1b1f;
  }
  * { margin: 0; padding: 0; box-sizing: border-box; }
  html, body {
    width: 1200px; height: 800px; overflow: hidden;
    background: var(--page-bg);
    font-family: "Montserrat", sans-serif;
  }
  .canvas { position: relative; width: 1200px; height: 800px; }

  .card {
    position: absolute;
    width: 436px; height: 272px;
    box-shadow: -2px 2px 4px rgba(0,0,0,0.25);
    overflow: hidden;
  }

  /* Front: black */
  .card--front { left: 193px; top: 101px; background: var(--card-black); color: var(--ink-light); }
  .card__stripes { position: absolute; inset: 0; width: 100%; height: 100%; }
  .identity {
    position: absolute; left: 0; right: 0; top: 78px;
    display: flex; flex-direction: column; align-items: center;
  }
  .identity__name {
    font-weight: 400; font-size: 21px; letter-spacing: 2.2px;
    line-height: 1; padding-bottom: 4px;
    width: 236px; text-align: center;
    border-bottom: 1px solid var(--ink-light);
  }
  .identity__title { margin-top: 6px; font-size: 11px; letter-spacing: 1.3px; }

  .contact {
    position: absolute; left: 0; right: 0; top: 176px;
    list-style: none; display: flex; flex-direction: column; align-items: center; gap: 10px;
    font-size: 8.5px; letter-spacing: 0.2px;
  }
  .contact__item { display: flex; align-items: center; gap: 8px; height: 14px; }
  .contact__icon { width: 9px; height: 9px; fill: var(--ink-light); }

  /* Back: white */
  .card--back { left: 567px; top: 424px; width: 441px; height: 276px; background: var(--card-white); }
  .brand {
    position: absolute; left: 66px; top: 104px; width: 308px;
    display: flex; align-items: center; gap: 12px;
  }
  .brand__square { width: 34px; height: 34px; background: var(--ink-dark); flex: none; }
  .brand__text { display: flex; flex-direction: column; }
  .brand__name { font-weight: 600; font-size: 15.5px; color: var(--ink-dark); letter-spacing: 0.3px; line-height: 1.1; }
  .brand__descriptor { font-weight: 600; font-size: 11px; color: var(--ink-grey); letter-spacing: 1.6px; line-height: 1.3; }
  .services {
    position: absolute; left: 67px; width: 306px; top: 150px;
    border-top: 1px solid var(--ink-dark);
    padding-top: 5px; text-align: center;
    font-size: 11.5px; font-weight: 500; color: var(--ink-dark); letter-spacing: 0.3px;
  }
</style>
</head>
<body>
<main class="canvas">

  <section class="card card--front" aria-label="Business card front">
    <svg class="card__stripes" viewBox="0 0 436 272" preserveAspectRatio="none" aria-hidden="true">
      <defs>
        <linearGradient id="stripe-fade-top" x1="1" y1="0" x2="0" y2="1">
          <stop offset="0" stop-color="var(--stripe)"/>
          <stop offset="1" stop-color="var(--stripe)" stop-opacity="0"/>
        </linearGradient>
        <linearGradient id="stripe-fade-bottom" x1="0" y1="1" x2="1" y2="0">
          <stop offset="0" stop-color="var(--stripe)" stop-opacity="0.2"/>
          <stop offset="1" stop-color="var(--stripe)"/>
        </linearGradient>
      </defs>
      <polygon points="56,0 104,0 0,96 0,52" fill="url(#stripe-fade-top)"/>
      <polygon points="129,0 160,0 0,140 0,112" fill="url(#stripe-fade-top)"/>
      <polygon points="436,150 436,162 312,272 300,272" fill="url(#stripe-fade-bottom)"/>
      <polygon points="436,210 436,240 400,272 384,272" fill="url(#stripe-fade-bottom)"/>
      <polygon points="436,170 436,200 354,272 330,272" fill="url(#stripe-fade-bottom)" opacity="0.6"/>
    </svg>

    <header class="identity">
      <h1 class="identity__name">DARIO WHITCOMBE</h1>
      <p class="identity__title">PRINCIPAL</p>
    </header>

    <ul class="contact">
      <li class="contact__item">
        <svg class="contact__icon" viewBox="0 0 24 24" aria-hidden="true"><path d="M6.6 10.8a15.1 15.1 0 0 0 6.6 6.6l2.2-2.2a1 1 0 0 1 1-.25 11.4 11.4 0 0 0 3.6.57 1 1 0 0 1 1 1V20a1 1 0 0 1-1 1A17 17 0 0 1 3 4a1 1 0 0 1 1-1h3.5a1 1 0 0 1 1 1c0 1.25.2 2.45.57 3.57a1 1 0 0 1-.25 1z"/></svg>
        <span>+12 345 678 90</span>
      </li>
      <li class="contact__item">
        <svg class="contact__icon" viewBox="0 0 24 24" aria-hidden="true"><path d="M2 5h20v14H2z M2 5l10 8 10-8" fill="var(--ink-light)" stroke="#000" stroke-width="1.5"/></svg>
        <span>email@yourcompany.com</span>
      </li>
      <li class="contact__item">
        <svg class="contact__icon" viewBox="0 0 24 24" aria-hidden="true"><path d="M12 2a7 7 0 0 0-7 7c0 5.2 7 13 7 13s7-7.8 7-13a7 7 0 0 0-7-7zm0 9.5A2.5 2.5 0 1 1 12 6.5a2.5 2.5 0 0 1 0 5z"/></svg>
        <span>Company address line</span>
      </li>
    </ul>
  </section>

  <section class="card card--back" aria-label="Business card back">
    <div class="brand">
      <span class="brand__square" aria-hidden="true"></span>
      <div class="brand__text">
        <p class="brand__name">DARIO WHITCOMBE, CPA, LLC</p>
        <p class="brand__descriptor">CERTIFIED PUBLIC ACCOUNTANT</p>
      </div>
    </div>
    <p class="services">Accounting, Tax &amp; Consulting Services</p>
  </section>

</main>
</body>
</html>
```